Brook Refrigeration. Refrigeration and air conditioning specialists.

We need a website to promote our business. We would a modern simple design using the colours from our logo and black. We want it to be fun but proffesional.

Target Market(s)

Commercial

Number of Pages Required

4 page

Requirements
Must have
• Home Page, About Us, Services and Contact Us.
• 24/7 365 days service available.
• Brook Refrigeration's dedicated team specialises in commercial refrigeration and air conditioning equipment.
• Based in Westmere, we cover Harbour City Metro and surrounding areas.
Nice to have
• KNOWLEDGE . EXPERIENCE . PASSION in bold.
• Our experienced and highly trained technicians provide extensive knowledge and exceptional skills for your commercial refrigeration and air conditioning requirements.
• Pictures of commercial refrigeration.
Should not have
• No mention of domestic services.

```html
<!DOCTYPE html>
<html lang="en">
<head>
<meta charset="utf-8">
<title>Brook Refrigeration</title>
<link rel="stylesheet" href="https://fonts.googleapis.com/css2?family=Montserrat:wght@400;600;700;800&family=Open+Sans:wght@400;600&display=swap">
<style>
:root{
  --lime:#86e03c;
  --ink:#1f1f1f;
  --text:#3a3a3a;
  --muted:#6b6b6b;
  --panel:#f1efef;
  --card:#ebeaea;
  --tile:#e1e1e1;
  --footer:#2b2b2b;
  --white:#ffffff;
  --field:#ffffff;
}
*{box-sizing:border-box;margin:0;padding:0}
html,body{width:1200px;height:3888px;overflow:hidden}
body{position:relative;background:var(--white);font-family:"Open Sans",Arial,sans-serif;color:var(--text)}
.abs{position:absolute}

/* header */
.site-header{left:0;top:0;width:1200px;height:137px;background:var(--white)}
.brand{left:130px;top:26px;font-family:"Montserrat",Arial,sans-serif;font-weight:800;color:var(--lime);line-height:1;letter-spacing:1px}
.brand .big{display:block;font-size:54px}
.brand .small{display:block;font-size:16px;margin-top:8px;letter-spacing:1.5px}
.call{left:700px;top:30px}
.call-label{left:760px;top:30px;font:700 13px "Montserrat",Arial,sans-serif;color:var(--ink)}
.call-number{left:760px;top:44px;font:700 26px "Montserrat",Arial,sans-serif;color:var(--lime)}
.follow-label{left:972px;top:28px;font:700 11px "Montserrat",Arial,sans-serif;color:var(--ink)}
.social{top:47px;width:26px;height:26px;border-radius:50%;background:#1f3b73}
.nav{top:96px;left:692px;display:flex;font:700 14px "Montserrat",Arial,sans-serif;color:var(--ink)}
.nav a{display:block;height:28px;line-height:28px;padding:0 16px;color:var(--ink);text-decoration:none}
.nav a.active{background:var(--lime)}

/* hero */
.hero{left:0;top:137px;width:1200px;height:581px;background:linear-gradient(100deg,#6f7780 0%,#c9cdd1 22%,#9aa1a8 38%,#d8dbde 55%,#b9bec3 72%,#e7e9ea 100%)}
.hero-band{left:793px;top:293px;width:407px;height:238px;background:rgba(134,224,60,.72)}
.hero-title{left:842px;top:356px;font:800 39px/47px "Montserrat",Arial,sans-serif;color:var(--white);letter-spacing:1px}
.dots{left:544px;top:664px;display:flex;gap:18px}
.dots span{width:10px;height:10px;border-radius:50%;background:var(--white)}
.dots span.on{background:var(--lime)}

/* welcome */
.welcome-kicker{left:0;width:1200px;top:780px;text-align:center;font:700 20px "Montserrat",Arial,sans-serif;color:var(--ink)}
.kicker-line{top:789px;width:120px;height:5px;border-top:1px solid #bbb;border-bottom:1px solid #bbb}
.welcome-title{left:0;width:1200px;top:816px;text-align:center;font:800 31px "Montserrat",Arial,sans-serif;color:var(--lime)}
.welcome-copy{left:360px;width:480px;top:876px;text-align:center;font-size:13px;line-height:20px;color:var(--text)}
.btn{background:var(--lime);color:var(--ink);font:700 12px "Montserrat",Arial,sans-serif;text-align:center;line-height:34px;height:34px}
.feature{top:1070px;width:236px;height:304px;background:var(--card);text-align:center}
.feature .icon{position:absolute;left:78px;top:42px;width:80px;height:80px;border-radius:50%;background:var(--lime);display:flex;align-items:center;justify-content:center}
.feature h3{position:absolute;left:0;width:100%;top:160px;font:700 14px/20px "Montserrat",Arial,sans-serif;color:var(--ink)}
.feature p{position:absolute;left:30px;width:176px;top:206px;font-size:11px;line-height:16px;color:var(--muted)}

/* services */
.services{left:0;top:1467px;width:1200px;height:731px;background:var(--panel)}
.services-title{left:137px;top:1550px;font:700 26px "Montserrat",Arial,sans-serif;color:var(--ink)}
.svc-icon{left:135px;width:60px;height:60px;border-radius:50%;background:var(--lime);display:flex;align-items:center;justify-content:center}
.svc-text{left:222px;width:320px;font-size:14px;line-height:20px;color:var(--ink)}
.fridge-visual{left:669px;top:1550px;width:394px;height:575px;background:linear-gradient(180deg,#2f76c4 0 6%,#f4f6f7 6% 82%,#1c1c1c 82% 100%)}

/* who we serve */
.serve-title{left:0;width:1200px;top:2282px;text-align:center;font:700 26px "Montserrat",Arial,sans-serif;color:var(--ink)}
.title-rule{height:3px;background:var(--ink)}
.serve-visual{left:181px;top:2410px;width:454px;height:454px;background:linear-gradient(90deg,#fff 0 3%,#d8dadc 3% 44%,#fff 44% 57%,#d8dadc 57% 97%,#fff 97%)}
.tile{width:156px;height:146px;background:var(--tile);text-align:center}
.tile svg{position:absolute;left:50%;top:30px;transform:translateX(-50%)}
.tile span{position:absolute;left:0;width:100%;top:100px;font:700 12px "Montserrat",Arial,sans-serif;color:var(--ink)}

/* contact */
.contact{left:0;top:2942px;width:1200px;height:578px;background:linear-gradient(100deg,#6fe02c 0%,#8ff04b 40%,#7fd84a 70%,#9be85e 100%)}
.contact-title{left:0;width:1200px;top:3016px;text-align:center;font:700 26px "Montserrat",Arial,sans-serif;color:var(--ink)}
.info-icon{left:172px;width:44px;height:44px;border-radius:50%;background:#3a3a3a;display:flex;align-items:center;justify-content:center}
.info-text{left:242px;font-size:14px;line-height:20px;color:var(--ink)}
.info-text small{display:block;font-size:10px;text-transform:uppercase}
.field{background:var(--field);font:600 11px "Montserrat",Arial,sans-serif;color:var(--ink);padding:11px 12px;text-transform:uppercase}
.submit{left:601px;top:3383px;width:127px;height:44px;background:#222;color:var(--white);font:700 15px "Montserrat",Arial,sans-serif;text-align:center;line-height:44px}

/* footer */
.site-footer{left:0;top:3520px;width:1200px;height:368px;background:var(--footer)}
.footer-brand{left:130px;top:3590px;font-family:"Montserrat",Arial,sans-serif;font-weight:800;color:var(--lime);line-height:1}
.footer-brand .big{display:block;font-size:70px}
.footer-brand .small{display:block;font-size:19px;margin-top:14px;letter-spacing:1.5px}
.vrule{top:3580px;width:1px;height:190px;background:#4a4a4a}
.footer-head{top:3580px;font:700 12px "Montserrat",Arial,sans-serif;color:var(--white)}
.footer-menu{left:604px;top:3612px;font-size:12px;line-height:18px;color:var(--white);list-style:none}
.footer-social{left:930px;font-size:12px;color:var(--white);display:flex;align-items:center;gap:12px}
.footer-social i{display:block;width:24px;height:24px;border-radius:50%;background:#2f5aa8}
.hrule{left:130px;top:3797px;width:940px;height:1px;background:#444}
.copyright{left:0;width:1200px;top:3834px;text-align:center;font-size:11px;color:#cfcfcf}
</style>
</head>
<body>

<header class="abs site-header">
  <div class="abs brand"><span class="big">BROOK</span><span class="small">REFRIGERATION</span></div>
  <svg class="abs call" width="34" height="34" viewBox="0 0 24 24"><path d="M6.6 10.8a15 15 0 0 0 6.6 6.6l2.2-2.2c.3-.3.7-.4 1-.2 1.1.4 2.3.6 3.6.6.6 0 1 .4 1 1V20c0 .6-.4 1-1 1A17 17 0 0 1 3 4c0-.6.4-1 1-1h3.5c.6 0 1 .4 1 1 0 1.3.2 2.5.6 3.6.1.3 0 .7-.2 1z" fill="#1f1f1f"/></svg>
  <div class="abs call-label">CALL US NOW</div>
  <div class="abs call-number">888.888.8888</div>
  <div class="abs follow-label">FOLLOW US</div>
  <span class="abs social" style="left:972px"></span>
  <span class="abs social" style="left:1006px;background:#1da1f2"></span>
  <span class="abs social" style="left:1040px"></span>
  <nav class="abs nav">
    <a class="active" href="#">HOME</a><a href="#">ABOUT US</a><a href="#">SERVICES</a><a href="#">CONTACT US</a>
  </nav>
</header>

<section class="abs hero" role="img" aria-label="Stainless steel commercial cool room doors and fridges"></section>
<div class="abs hero-band"></div>
<h1 class="abs hero-title">KNOWLEDGE .<br>EXPERIENCE .<br>PASSION</h1>
<div class="abs dots"><span></span><span></span><span class="on"></span><span></span><span></span></div>

<div class="abs kicker-line" style="left:435px"></div>
<div class="abs kicker-line" style="left:645px"></div>
<div class="abs welcome-kicker">WELCOME TO</div>
<h2 class="abs welcome-title">BROOK REFRIGERATION</h2>
<p class="abs welcome-copy">At vero eos et accusamus et iusto odio dignissimos ducimus qui blanditiis praesentium voluptatum deleniti atque corrupti quos dolores et quas molestias excepturi sint occaecati cupiditate non provident, similique sunt in culpa qui officia deserunt mollitia animi, id est laborum.</p>
<div class="abs btn" style="left:545px;top:995px;width:110px">READ MORE</div>

<div class="abs feature" style="left:111px">
  <div class="icon"><svg width="40" height="40" viewBox="0 0 24 24"><path d="M12 8a4 4 0 1 0 0 8 4 4 0 0 0 0-8zm9 5.5v-3l-2.4-.5-.7-1.6 1.3-2-2.1-2.1-2 1.3-1.6-.7L13 2.5h-3l-.5 2.4-1.6.7-2-1.3-2.1 2.1 1.3 2-.7 1.6-2.4.5v3l2.4.5.7 1.6-1.3 2 2.1 2.1 2-1.3 1.6.7.5 2.4h3l.5-2.4 1.6-.7 2 1.3 2.1-2.1-1.3-2 .7-1.6z" fill="#1f1f1f"/></svg></div>
  <h3>Customer<br>SATISIFACTION</h3>
  <p>At vero eos et accusamus et iusto odio dignissimos ducimus qui blanditiis praesentium voluptatum deleniti</p>
</div>
<div class="abs feature" style="left:363px">
  <div class="icon"><svg width="40" height="40" viewBox="0 0 24 24"><path d="M9 4h6v3h5v12H4V7h5zm2 1v2h2V5zM4 11h16v1H4z" fill="#1f1f1f"/></svg></div>
  <h3>15+<br>EXPERIENCE</h3>
  <p>At vero eos et accusamus et iusto odio dignissimos ducimus qui blanditiis praesentium voluptatum deleniti</p>
</div>
<div class="abs feature" style="left:609px">
  <div class="icon"><svg width="40" height="40" viewBox="0 0 24 24"><circle cx="12" cy="7.5" r="4.5" fill="#1f1f1f"/><path d="M3 21c0-5 4-8 9-8s9 3 9 8z" fill="#1f1f1f"/></svg></div>
  <h3>EXPERT<br>TECHNICIANS</h3>
  <p>At vero eos et accusamus et iusto odio dignissimos ducimus qui blanditiis praesentium voluptatum deleniti</p>
</div>
<div class="abs feature" style="left:853px">
  <div class="icon"><svg width="40" height="40" viewBox="0 0 24 24"><path d="M12 3c5 0 9 3.4 9 7.5S17 18 12 18l-5 3 1-4c-3-1.3-5-3.7-5-6.5C3 6.4 7 3 12 3z" fill="#1f1f1f"/><path d="M8 9h8M8 12h6" stroke="#86e03c" stroke-width="1.6"/></svg></div>
  <h3>RELIABLE<br>CONSULTING</h3>
  <p>At vero eos et accusamus et iusto odio dignissimos ducimus qui blanditiis praesentium voluptatum deleniti</p>
</div>

<section class="abs services"></section>
<h2 class="abs services-title">OUR SERVICES</h2>

<div class="abs svc-icon" style="top:1638px"><svg width="30" height="30" viewBox="0 0 24 24"><path d="M6.6 10.8a15 15 0 0 0 6.6 6.6l2.2-2.2c.3-.3.7-.4 1-.2 1.1.4 2.3.6 3.6.6.6 0 1 .4 1 1V20c0 .6-.4 1-1 1A17 17 0 0 1 3 4c0-.6.4-1 1-1h3.5c.6 0 1 .4 1 1 0 1.3.2 2.5.6 3.6.1.3 0 .7-.2 1z" fill="#1f1f1f"/></svg></div>
<p class="abs svc-text" style="top:1658px">24/7 365 days service available</p>

<div class="abs svc-icon" style="top:1736px"><svg width="32" height="32" viewBox="0 0 24 24"><circle cx="12" cy="8" r="3.2" fill="#1f1f1f"/><circle cx="5.5" cy="10" r="2.3" fill="#1f1f1f"/><circle cx="18.5" cy="10" r="2.3" fill="#1f1f1f"/><path d="M6 20c0-4 2.7-7 6-7s6 3 6 7zM1 19c0-3 1.8-5.5 4.5-5.5 1 0 1.8.3 2.5.8-1.3 1.3-2 3-2.2 4.7zM23 19c0-3-1.8-5.5-4.5-5.5-1 0-1.8.3-2.5.8 1.3 1.3 2 3 2.2 4.7z" fill="#1f1f1f"/></svg></div>
<p class="abs svc-text" style="top:1736px">Brook Refrigeration's dedicated team specialises in commercial refrigeration and air conditioning equipment.</p>

<div class="abs svc-icon" style="top:1836px"><svg width="30" height="30" viewBox="0 0 24 24"><path d="M2 5l6-2 8 2 6-2v16l-6 2-8-2-6 2z" fill="#1f1f1f"/><path d="M8 3v16M16 5v16" stroke="#86e03c" stroke-width="1.2"/></svg></div>
<p class="abs svc-text" style="top:1846px">Based in Westmere, we cover Harbour City Metro and surrounding areas.</p>

<div class="abs svc-icon" style="top:1937px"><svg width="28" height="30" viewBox="0 0 24 24"><rect x="5" y="2" width="14" height="20" rx="2" fill="#1f1f1f"/><path d="M5 9h14M8 5v2M8 12v4" stroke="#86e03c" stroke-width="1.4"/></svg></div>
<p class="abs svc-text" style="top:1927px">Our experienced and highly trained technicians provide extensive knowledge and exceptional skills for your commercial refrigeration and air conditioning requirements.</p>

<div class="abs btn" style="left:140px;top:2068px;width:108px">READ MORE</div>
<div class="abs fridge-visual" role="img" aria-label="Double glass door merchandiser fridge"></div>

<h2 class="abs serve-title">WHO WE SERVE</h2>
<div class="abs title-rule" style="left:571px;top:2328px;width:58px"></div>
<div class="abs serve-visual" role="img" aria-label="Two single glass door cold drinks fridges, one with its door open"></div>

<div class="abs tile" style="left:690px;top:2465px">
  <svg width="60" height="50" viewBox="0 0 24 20"><path d="M3 19V6h6v13zM10 19V2h7v17zM18 19V8h4v11z" fill="#1f1f1f"/><path d="M4.5 8h1M7 8h1M4.5 11h1M7 11h1M4.5 14h1M7 14h1M12 4h1M14.5 4h1M12 7h1M14.5 7h1M12 10h1M14.5 10h1M12 13h1M14.5 13h1M19.5 10h1M19.5 13h1" stroke="#e1e1e1" stroke-width="1.2"/><path d="M1 19.5h22" stroke="#1f1f1f"/></svg>
  <span>HOTELS</span>
</div>
<div class="abs tile" style="left:863px;top:2465px">
  <svg width="60" height="50" viewBox="0 0 24 20"><circle cx="11" cy="10" r="7" fill="none" stroke="#1f1f1f" stroke-width="2"/><circle cx="11" cy="10" r="3.5" fill="#1f1f1f"/><path d="M20 2v16M18.5 2v5h3V2" stroke="#1f1f1f" stroke-width="1.4" fill="none"/><path d="M2 2v5M1 2v4c0 1 2 1 2 0V2M2 7v11" stroke="#1f1f1f" stroke-width="1.2" fill="none"/></svg>
  <span>RESTAURANTS</span>
</div>
<div class="abs tile" style="left:690px;top:2628px">
  <svg width="60" height="50" viewBox="0 0 24 20"><path d="M2 8l2-6h16l2 6z" fill="#1f1f1f"/><path d="M3 9h18v10H3z" fill="none" stroke="#1f1f1f" stroke-width="1.6"/><path d="M10 19v-6h4v6z" fill="#1f1f1f"/><path d="M6 2l-1 6M10 2v6M14 2v6M18 2l1 6" stroke="#e1e1e1" stroke-width=".8"/></svg>
  <span>GOURMET MARKETS</span>
</div>
<div class="abs tile" style="left:863px;top:2628px">
  <svg width="60" height="50" viewBox="0 0 24 20"><path d="M5 19V3h14v16z" fill="#1f1f1f"/><path d="M12 5v5M9.5 7.5h5" stroke="#e1e1e1" stroke-width="1.6"/><path d="M7.5 12h2M14.5 12h2M7.5 15h2M14.5 15h2" stroke="#e1e1e1" stroke-width="1.2"/><path d="M11 19v-4h2v4z" fill="#e1e1e1"/></svg>
  <span>HOSPITALS</span>
</div>

<section class="abs contact" role="img" aria-label="Green toned backdrop of a commercial fridge aisle"></section>
<h2 class="abs contact-title">CONTACT US</h2>
<div class="abs title-rule" style="left:571px;top:3062px;width:58px"></div>

<div class="abs info-icon" style="top:3155px"><svg width="18" height="20" viewBox="0 0 24 24"><path d="M12 2a7 7 0 0 0-7 7c0 5 7 13 7 13s7-8 7-13a7 7 0 0 0-7-7zm0 9.5A2.5 2.5 0 1 1 12 6.5a2.5 2.5 0 0 1 0 5z" fill="#fff"/></svg></div>
<p class="abs info-text" style="top:3156px">57 Foundry Road<br>Marlow, IL 60499</p>
<div class="abs info-icon" style="top:3248px"><svg width="18" height="18" viewBox="0 0 24 24"><path d="M6.6 10.8a15 15 0 0 0 6.6 6.6l2.2-2.2c.3-.3.7-.4 1-.2 1.1.4 2.3.6 3.6.6.6 0 1 .4 1 1V20c0 .6-.4 1-1 1A17 17 0 0 1 3 4c0-.6.4-1 1-1h3.5c.6 0 1 .4 1 1 0 1.3.2 2.5.6 3.6.1.3 0 .7-.2 1z" fill="#fff"/></svg></div>
<p class="abs info-text" style="top:3246px"><small>Call us</small>888.888.8888</p>
<div class="abs info-icon" style="top:3335px"><svg width="18" height="16" viewBox="0 0 24 20"><path d="M2 2h20v16H2z" fill="#fff"/><path d="M2 2l10 8 10-8" stroke="#3a3a3a" stroke-width="1.6" fill="none"/></svg></div>
<p class="abs info-text" style="top:3333px"><small>E mail us</small>info@brookrefrigeration.com</p>

<div class="abs field" style="left:601px;top:3141px;width:214px;height:37px">Name</div>
<div class="abs field" style="left:831px;top:3141px;width:214px;height:37px">E mail</div>
<div class="abs field" style="left:601px;top:3196px;width:214px;height:37px">Phone</div>
<div class="abs field" style="left:831px;top:3196px;width:214px;height:37px">Subject</div>
<div class="abs field" style="left:601px;top:3250px;width:444px;height:114px">Message</div>
<div class="abs submit">SUBMIT</div>

<footer class="abs site-footer"></footer>
<div class="abs footer-brand"><span class="big">BROOK</span><span class="small">REFRIGERATION</span></div>
<div class="abs vrule" style="left:472px"></div>
<div class="abs vrule" style="left:793px"></div>
<div class="abs footer-head" style="left:604px">MENU</div>
<ul class="abs footer-menu"><li>Home</li><li>About Us</li><li>Services</li><li>Contact Us</li></ul>
<div class="abs footer-head" style="left:928px">CONNECT WITH US</div>
<div class="abs footer-social" style="top:3616px"><i></i>Facenote</div>
<div class="abs footer-social" style="top:3656px"><i style="background:#1da1f2"></i>Chirper</div>
<div class="abs footer-social" style="top:3696px"><i style="background:#1f3b73"></i>Linkwork</div>
<div class="abs hrule"></div>
<p class="abs copyright">Copyrights @ 2018 All Rights Reserved</p>

</body>
</html>
```